Plotvista Caribbean

We need a vibrant, user friendly and exciting website for our land search company called "plotVista" This application will help individuals locate and or list lots for sale within the Caribbean. We will offer a small cash back incentive to buyers that purchase land from our site, and we will charge a 1%-2% success fee to our sellers once a successful transaction is made. We would like to become a match making site, matching buyers and sellers on our platform. We will also include a service directory and marketing advertisement spot for other service providers for a fee. We would like to see a webdesign incorporating Caribbean colors (blue, green and yellow) with very modern clean lines, very picturesque and easy to use.

Industry/Entity Type

Real Estate

Coding

Coded - Design and coding required

Number of Pages Required

5+ page

Font styles to use
Sans Serif

Colors
ffffff
85acd3
b768aa
dbdbdb

Requirements
Nice to have
• Scenic photos of the ocean and beautiful landscape

```html
<!DOCTYPE html>
<html lang="en">
<head>
<meta charset="utf-8">
<title>plotVista — Find and list land in the Caribbean</title>
<link rel="stylesheet" href="https://fonts.googleapis.com/css2?family=Raleway:wght@400;500;600&family=Roboto:wght@400;500&family=Open+Sans:ital,wght@1,400&display=swap">
<style>
:root{
  --white:#ffffff;
  --sky:#85acd3;
  --orchid:#b768aa;
  --mist:#dbdbdb;
  --ink:#4a4a4a;
  --muted:#7a7a7a;
  --panel:#f5f6f8;
  --footer-bar:#3b3b3b;
}
*{margin:0;padding:0;box-sizing:border-box}
html,body{width:1200px;height:2632px;overflow:hidden;background:var(--white)}
body{font-family:"Roboto",Arial,sans-serif;color:var(--ink);position:relative}
section,header,footer{position:absolute;left:0;width:1200px}
.abs{position:absolute}
.heading{font-family:"Raleway",sans-serif;font-weight:500;color:#555;letter-spacing:.5px}
.body-text{font-size:13px;line-height:25px;color:var(--muted)}

/* header */
.site-header{top:0;height:82px;background:var(--white)}
.brand{left:86px;top:18px;font-family:"Raleway",sans-serif;font-weight:600;font-size:32px;color:var(--orchid)}
.main-nav{right:86px;top:33px;display:flex;gap:52px;font-size:12.5px;color:#666;list-style:none}
.main-nav .current{color:var(--orchid)}

/* hero */
.hero{top:82px;height:527px;background:
  linear-gradient(180deg,#5d7d9b 0%,#8fa7b9 28%,#e7a04a 41%,#3f6b77 50%,#2f5a63 75%,#3b3c38 100%)}
.hero-arrow{top:240px;width:52px;height:52px;border:2px solid var(--white);border-radius:50%}
.hero-arrow.prev{left:24px}.hero-arrow.next{right:24px}
.hero-title{top:278px;width:100%;text-align:center;font-family:"Raleway",sans-serif;font-weight:600;font-size:40px;color:var(--white);letter-spacing:1px}
.hero-text{top:338px;width:100%;text-align:center;font-size:12.5px;line-height:26px;color:var(--white)}
.ghost-btn{border:1.5px solid var(--white);color:var(--white);font-size:13px;text-align:center;line-height:40px}
.hero-btn{top:411px;left:509px;width:182px;height:43px}

/* welcome */
.welcome{top:609px;height:510px}
.welcome-title{top:42px;width:100%;text-align:center;font-size:25px}
.divider{left:563px;width:74px;height:14px}
.welcome-text{top:104px;width:100%;text-align:center}
.feature{top:216px;width:300px;text-align:center}
.feature-icon{width:120px;height:120px;border-radius:50%;margin:0 auto;display:flex;align-items:center;justify-content:center}
.feature-name{margin-top:16px;font-size:18px}
.feature-text{margin-top:10px}

/* about + testimonials */
.about-band{top:1119px;height:340px;background:var(--panel)}
.section-title{font-size:25px}
.outline-btn{border:1.5px solid #3c7fbf;color:#3c7fbf;font-size:13px;font-weight:500;text-align:center;line-height:38px;border-radius:2px}
.portrait{left:512px;top:98px;width:126px;height:126px;border-radius:50%;background:radial-gradient(circle at 50% 40%,#c99c80,#6b4a3a)}
.quote-mark{font-family:Georgia,serif;font-size:26px;color:#666}
.author{font-size:13.5px;font-weight:500;color:var(--orchid)}

/* platform banner */
.platform{top:1459px;height:379px;background:linear-gradient(160deg,#6fa3d6 0%,#3f86c4 35%,#8fbde2 65%,#4c8fc8 100%)}
.platform-title{top:104px;width:100%;text-align:center;font-family:"Raleway",sans-serif;font-size:24px;color:var(--white)}
.platform-text{top:174px;width:100%;text-align:center;font-size:12.5px;line-height:26px;color:var(--white)}
.platform-btn{top:251px;left:489px;width:221px;height:39px;font-size:12.5px;line-height:36px}

/* media */
.media{top:1838px;height:465px}
.video-frame{left:84px;top:97px;width:433px;height:187px;background:linear-gradient(180deg,#b9c95a 0%,#8aa33a 45%,#4f7a2a 100%)}
.play{left:187px;top:64px;width:58px;height:58px;border:2px solid var(--white);border-radius:50%}
.read-link{font-size:12px;font-weight:500;color:var(--orchid);text-decoration:underline;letter-spacing:.5px}
.post-thumb{left:598px;width:153px;height:117px}
.post-title{left:773px;font-size:13px;font-weight:500;color:#444}
.post-meta{left:773px;font-family:"Open Sans",sans-serif;font-style:italic;font-size:12.5px;color:var(--orchid);display:flex;gap:16px;align-items:center}
.post-text{left:773px;width:340px}

/* footer */
.site-footer{top:2303px;height:263px;background:var(--panel)}
.footer-title{top:54px;font-family:"Raleway",sans-serif;font-weight:600;font-size:16px;color:#555}
.footer-list{top:97px;list-style:none;font-size:12.5px;color:#666}
.footer-list li{height:24px;display:flex;align-items:center;gap:16px}
.contact-list li{gap:14px}
.email-field{left:607px;top:137px;width:211px;height:34px;border:1px solid #ccc;background:var(--white);font-size:12.5px;color:#555;padding-left:12px;line-height:32px}
.subscribe{left:607px;top:184px;width:82px;height:27px;background:var(--orchid);color:var(--white);font-size:10.5px;font-weight:500;text-align:center;line-height:27px;border-radius:2px}
.socials{left:901px;top:162px;display:flex;gap:8px}
.socials span{width:36px;height:36px;border:1.5px solid #bbb;border-radius:50%}
.copyright{top:2566px;height:66px;background:var(--footer-bar);color:var(--white);font-size:12.5px;text-align:center;line-height:66px}
</style>
</head>
<body>

<header class="site-header">
  <div class="abs brand">plotVista</div>
  <ul class="abs main-nav">
    <li class="current">HOME</li><li>ABOUT US</li><li>SERVICES</li><li>LANDSCAPE</li><li>NEWS</li><li>CONTACT US</li>
  </ul>
</header>

<section class="hero" role="img" aria-label="Mountain lake at sunset with rocky shoreline">
  <svg class="abs hero-arrow prev" viewBox="0 0 52 52"><path d="M29 17 L20 26 L29 35" fill="none" stroke="#fff" stroke-width="3.5"/></svg>
  <svg class="abs hero-arrow next" viewBox="0 0 52 52"><path d="M23 17 L32 26 L23 35" fill="none" stroke="#fff" stroke-width="3.5"/></svg>
  <h1 class="abs hero-title">PLOTVISTA</h1>
  <p class="abs hero-text">Sed ut perspiciatis unde omnis iste natus error sit voluptatem accusantium doloremque laudantium, totam rem aperiam,<br>eaque ipsa quae ab illo inventore veritatis et quasi architecto beatae vitae dicta sunt explicabo.</p>
  <div class="abs ghost-btn hero-btn">READ MORE INFO</div>
</section>

<section class="welcome">
  <h2 class="abs heading welcome-title">WELCOME TO PLOTVISTA</h2>
  <svg class="abs divider" style="top:85px" viewBox="0 0 74 14"><g fill="none" stroke="#b768aa" stroke-width="1.6"><circle cx="7" cy="7" r="5"/><circle cx="37" cy="7" r="5"/><circle cx="67" cy="7" r="5"/><path d="M12 7H32M42 7H62"/></g></svg>
  <p class="abs body-text welcome-text">Sed ut perspiciatis unde omnis iste natus error sit voluptatem accusantium doloremque laudantium, totam rem aperiam, eaque ipsa<br>quae ab illo inventore veritatis et quasi architecto beatae vitae dicta sunt explicabo.</p>

  <div class="abs feature" style="left:101px">
    <div class="feature-icon" style="background:var(--sky)">
      <svg width="70" height="70" viewBox="0 0 70 70" fill="#fff"><circle cx="30" cy="20" r="12"/><path d="M10 62c0-16 9-26 20-26 6 0 10 2 13 5v21z"/><text x="46" y="60" font-size="24" font-family="Arial" font-weight="bold">$</text></svg>
    </div>
    <h3 class="heading feature-name">BUYERS</h3>
    <p class="body-text feature-text">Sed ut perspiciatis unde omnis iste natus error sit<br>voluptatem accusantium doloremque laudantium,<br>beatae vitae dicta sunt explicabo.</p>
  </div>
  <div class="abs feature" style="left:448px">
    <div class="feature-icon" style="background:var(--orchid)">
      <svg width="76" height="60" viewBox="0 0 76 60" fill="#fff"><path d="M2 18l14-10 10 6-14 20z"/><path d="M74 18L60 8 50 14l14 20z"/><path d="M24 18l12-6 22 18c3 3 0 7-3 5L42 26l10 12c2 3-1 6-4 4L38 32l6 10c1 3-2 5-4 3l-8-9-8 6z"/></svg>
    </div>
    <h3 class="heading feature-name">SELLERS</h3>
    <p class="body-text feature-text">Sed ut perspiciatis unde omnis iste natus error sit<br>voluptatem accusantium doloremque laudantium,<br>beatae vitae dicta sunt explicabo.</p>
  </div>
  <div class="abs feature" style="left:794px">
    <div class="feature-icon" style="background:var(--sky)">
      <svg width="70" height="70" viewBox="0 0 70 70" fill="none" stroke="#fff" stroke-width="3"><path d="M20 8v40M12 40l8 10 8-10"/><path d="M50 62V22M42 30l8-10 8 10"/><circle cx="35" cy="34" r="11"/><text x="30" y="40" font-size="16" font-family="Arial" fill="#fff" stroke="none">$</text></svg>
    </div>
    <h3 class="heading feature-name">TRANSACTION</h3>
    <p class="body-text feature-text">Sed ut perspiciatis unde omnis iste natus error sit<br>voluptatem accusantium doloremque laudantium,<br>beatae vitae dicta sunt explicabo.</p>
  </div>
</section>

<section class="about-band">
  <h2 class="abs heading section-title" style="left:88px;top:36px">ABOUT US</h2>
  <p class="abs body-text" style="left:88px;top:88px;width:378px;font-size:12.5px;line-height:22.5px;color:#666">Sed ut perspiciatis unde omnis iste natus error sit voluptatem accusantium doloremque laudantium, totam rem aperiam, eaque ipsa quae ab illo inventore veritatis et quasi architecto beatae vitae dicta sunt explicabo. Nemo enim ipsam voluptatem quia voluptas sit aspernatur aut odit aut fugit, sed quia consequuntur magni dolores eos qui ratione voluptatem sequi nesciunt.</p>
  <div class="abs outline-btn" style="left:88px;top:256px;width:125px;height:40px">READ MORE</div>

  <h2 class="abs heading section-title" style="left:512px;top:36px">TESTIMONIALS</h2>
  <div class="abs portrait" role="img" aria-label="Portrait photo of the reviewer"></div>
  <span class="abs quote-mark" style="left:658px;top:100px">“</span>
  <p class="abs body-text" style="left:677px;top:122px;width:434px;font-size:12.5px;line-height:22.5px;color:#666">Sed ut perspiciatis unde omnis iste natus error sit voluptatem accusan tium doloremque laudantium, totam rem aperiam, eaque ipsa quae ab illo inventore veritatis et quasi architecto beatae vitae dicta sunt explicabo. Nemo enim ipsam voluptatem sequi magni dolores eos qui ratione voluptatem sequi nesciunt.</p>
  <span class="abs quote-mark" style="left:985px;top:206px">”</span>
  <p class="abs author" style="left:677px;top:242px">Name : Dara Morrow</p>
  <p class="abs" style="left:677px;top:266px;font-size:11px;color:#888">Posed on 02 May 2017</p>
</section>

<section class="platform" role="img" aria-label="Curling blue ocean wave">
  <h2 class="abs platform-title">MATCHING BUYERS &amp; SELLERS ON OUR PLATFORM</h2>
  <svg class="abs divider" style="top:148px" viewBox="0 0 74 14"><g fill="none" stroke="#fff" stroke-width="1.6"><circle cx="7" cy="7" r="5"/><circle cx="37" cy="7" r="5"/><circle cx="67" cy="7" r="5"/><path d="M12 7H32M42 7H62"/></g></svg>
  <p class="abs platform-text">Sed ut perspiciatis unde omnis iste natus error sit voluptatem accusantium doloremque laudantium, totam rem aperiam, eaque ipsa<br>quae ab illo inventore veritatis et quasi architecto beatae vitae dicta sunt explicabo.</p>
  <div class="abs ghost-btn platform-btn">CLICK HERE FOR MORE INFO</div>
</section>

<section class="media">
  <h2 class="abs heading section-title" style="left:84px;top:38px">OUR VIDEO</h2>
  <div class="abs video-frame" role="img" aria-label="Terraced green rice fields in morning light">
    <svg class="abs play" viewBox="0 0 58 58"><path d="M23 18L39 29 23 40z" fill="#fff"/></svg>
  </div>
  <p class="abs body-text" style="left:84px;top:298px;width:440px;font-size:12.5px;line-height:25px;color:#666">Sed ut perspiciatis unde omnis iste natus error sit voluptatem accusantium doloremque laudantium, totam rem aperiam, eaque ipsa quae ab illo inventore verita et quasi architecto beatae vitae dicta sunt explicabo.</p>
  <span class="abs read-link" style="left:84px;top:398px">READ MORE &gt;&gt;</span>

  <h2 class="abs heading section-title" style="left:596px;top:38px">LATEST BLOG</h2>

  <div class="abs post-thumb" style="top:97px;background:linear-gradient(180deg,#3a6fa8 0%,#f0a040 45%,#2a5a8a 60%,#1f3b55 100%)" role="img" aria-label="Sunset over rocky sea shore"></div>
  <h3 class="abs post-title" style="top:100px">SED UT PERSPICIATIS UNDE</h3>
  <div class="abs post-meta" style="top:126px">
    <span><svg width="12" height="12" viewBox="0 0 12 12" fill="none" stroke="#b768aa" stroke-width="1.3"><rect x="1" y="2" width="10" height="9"/><path d="M1 5h10M4 0v3M8 0v3"/></svg> 1 month ago</span>
    <span><svg width="12" height="12" viewBox="0 0 12 12" fill="none" stroke="#b768aa" stroke-width="1.3"><path d="M1 6a5 4 0 1 1 3 3.6L2 11z"/></svg> 05 Comments</span>
  </div>
  <p class="abs body-text post-text" style="top:153px;font-size:12px;line-height:26px;color:#666">Sed ut perspiciatis unde omnis iste natus error sit voluptatem accusantium doloremque laudantium, totam rem</p>
  <div class="abs" style="left:773px;top:232px;width:339px;height:1px;background:var(--mist)"></div>

  <div class="abs post-thumb" style="top:253px;background:linear-gradient(180deg,#8fb8e0 0%,#c8d8e8 35%,#6f8f4a 60%,#3e5a2e 100%)" role="img" aria-label="Green sea cliffs under blue sky"></div>
  <h3 class="abs post-title" style="top:256px">SED UT PERSPICIATIS UNDE</h3>
  <div class="abs post-meta" style="top:282px">
    <span><svg width="12" height="12" viewBox="0 0 12 12" fill="none" stroke="#b768aa" stroke-width="1.3"><rect x="1" y="2" width="10" height="9"/><path d="M1 5h10M4 0v3M8 0v3"/></svg> 1 month ago</span>
    <span><svg width="12" height="12" viewBox="0 0 12 12" fill="none" stroke="#b768aa" stroke-width="1.3"><path d="M1 6a5 4 0 1 1 3 3.6L2 11z"/></svg> 05 Comments</span>
  </div>
  <p class="abs body-text post-text" style="top:309px;font-size:12px;line-height:26px;color:#666">Sed ut perspiciatis unde omnis iste natus error sit voluptatem accusantium doloremque laudantium, totam rem</p>
  <span class="abs read-link" style="left:600px;top:398px">READ MORE &gt;&gt;</span>
</section>

<footer class="site-footer">
  <h4 class="abs footer-title" style="left:125px">QUICK LINKS</h4>
  <ul class="abs footer-list" style="left:125px">
    <li><span>»</span>Home</li><li><span>»</span>About Us</li><li><span>»</span>Services</li><li><span>»</span>landscape</li><li><span>»</span>News</li><li><span>»</span>Contact Us</li>
  </ul>

  <h4 class="abs footer-title" style="left:323px">CONTACT US</h4>
  <ul class="abs footer-list contact-list" style="left:323px;top:102px">
    <li><svg width="13" height="12" viewBox="0 0 13 12" fill="#777"><path d="M1 4c0-2 3-3 5.5-3S12 2 12 4l-3 1-1-2H5L4 5z M3 6h7l2 5H1z"/></svg>(000)-555-0142 (Phone)</li>
    <li><svg width="13" height="12" viewBox="0 0 13 12" fill="#777"><rect x="3" y="0" width="7" height="4"/><rect x="0" y="4" width="13" height="5" rx="1"/><rect x="3" y="8" width="7" height="4"/></svg>(000)-555-0142 (Fax)</li>
    <li><svg width="13" height="10" viewBox="0 0 13 10" fill="none" stroke="#777" stroke-width="1.4"><rect x="1" y="1" width="11" height="8"/><path d="M1 1l5.5 4L12 1"/></svg><span style="text-decoration:underline">www.plotVista.com/</span></li>
    <li style="align-items:flex-start;height:auto;padding-top:4px"><svg width="13" height="14" viewBox="0 0 13 14" fill="#777"><path d="M6.5 0a4.5 4.5 0 0 1 4.5 4.5C11 8 6.5 14 6.5 14S2 8 2 4.5A4.5 4.5 0 0 1 6.5 0z"/><circle cx="6.5" cy="4.5" r="1.6" fill="#f5f6f8"/></svg><span style="line-height:15px">3350 Lorem Ipsum Dummy Text<br>Lorem Ipsum</span></li>
  </ul>

  <h4 class="abs footer-title" style="left:607px">NEWSLETTER</h4>
  <p class="abs" style="left:607px;top:93px;width:230px;font-size:12.5px;line-height:21px;color:#666">Register Your email address to get information about us</p>
  <div class="abs email-field">Email Address</div>
  <div class="abs subscribe">SUBSCRIBE</div>

  <h4 class="abs footer-title" style="left:903px">FOLLOW US</h4>
  <p class="abs" style="left:903px;top:92px;width:200px;font-size:12px;line-height:20px;color:#666">Lorem ipsum dolor sit amet, conse ctetur adipiscing elit. Nulla in purus nibh. Donec ornare</p>
  <div class="abs socials"><span></span><span></span><span></span><span></span><span></span></div>
</footer>

<div class="abs copyright" style="left:0;width:1200px">© Copyright 2017 plotVista.All Rights Reserved</div>

</body>
</html>
```